Business Cards Needed for Innovative Healthcare Marketing Company

We are a marketing company focused on healthcare. Our company is all about rebranding yourself renewing your image and generating results. The phoenix stands for "reborn" or "rising" which we provide new brands for our clients we take their old brands and renew it with creativity and innovation. I am looking for a business card with color dimension. I have attached an example of a card I think has the look and feel of what I am trying to accomplish. I like that the card example has black and grey font colors, I like the font placement and the small logo, I really like the use of the colors on the right those are the colors of my logo. My logo is phoenix so maybe incorporating flames similar to that design. I would like the back a solid color maybe red with an opaque version of the logo and website. As a marketing company I am always open to creative liberty!

Target Market(s)

Doctors and business professionals.

Industry/Entity Type

Marketing

Contact Information for Business Card

Valcorne Health Care Marketing
Marla Tenwick- CEO
#(512)638-2974
email-marla@valcorne.com
website- valcorne.com

Font styles to use
Sans Serif

Colors
ec1f27
f37122
ffc214
fbed22
fbf289
f04a50

Requirements
Must have
• The logo and required information
Nice to have
• icons by the information
Should not have
• child like font

```html
<!DOCTYPE html>
<html lang="en">
<head>
<meta charset="utf-8">
<title>Valcorne Health Care Marketing – Business Cards</title>
<link rel="stylesheet" href="https://fonts.googleapis.com/css2?family=Josefin+Sans:wght@300&family=Open+Sans:wght@400;700&display=swap">
<style>
  :root {
    --backdrop: #e4e4e4;
    --card-white: #ffffff;
    --card-black: #000000;
    --brand-red: #9b1b1f;
    --art-red: #a11d21;
    --art-red-deep: #7e1518;
    --ink: #2a2a2a;
  }
  * { margin: 0; padding: 0; box-sizing: border-box; }
  html, body { width: 1200px; height: 900px; overflow: hidden; }
  body {
    background: var(--backdrop);
    position: relative;
    font-family: "Open Sans", Arial, sans-serif;
  }
  .card {
    position: absolute;
    top: 170px;
    width: 347px;
    height: 561px;
    overflow: hidden;
    text-align: center;
  }
  .card--front { left: 259px; background: var(--card-white); }
  .card--back { left: 631px; background: var(--card-black); }

  .wordmark {
    position: absolute;
    left: 0; right: 0;
    color: var(--brand-red);
    font-family: "Josefin Sans", Arial, sans-serif;
    font-weight: 300;
    line-height: 1;
  }
  .wordmark__name { display: block; font-size: 52px; letter-spacing: 1px; }
  .wordmark__line { display: block; font-size: 15.5px; letter-spacing: 1px; margin-top: 12px; }
  .card--front .wordmark { top: 80px; }
  .card--back .wordmark { top: 240px; }

  .person { position: absolute; top: 206px; left: 0; right: 0; }
  .person__name { color: var(--brand-red); font-weight: 700; font-size: 19px; letter-spacing: 0.2px; line-height: 26px; }
  .person__role { color: var(--ink); font-size: 14px; line-height: 20px; }

  .contact { position: absolute; top: 272px; left: 0; right: 0; list-style: none; color: var(--ink); font-size: 14.5px; line-height: 20px; }

  .flame-art { position: absolute; left: 0; bottom: 0; width: 347px; display: block; }
</style>
</head>
<body>

  <section class="card card--front" aria-label="Card front">
    <div class="wordmark">
      <span class="wordmark__name">VALCORNE</span>
      <span class="wordmark__line">HEALTH CARE MARKETING</span>
    </div>
    <div class="person">
      <p class="person__name">MARLA TENWICK</p>
      <p class="person__role">CEO</p>
    </div>
    <ul class="contact">
      <li>(512)638-2974</li>
      <li>marla@valcorne.com</li>
      <li>www.valcorne.com</li>
    </ul>
    <svg class="flame-art" width="347" height="206" viewBox="0 0 347 206" role="img" aria-label="Red phoenix wing and flame illustration rising across the bottom of the card">
      <defs>
        <linearGradient id="front-art" x1="0" y1="0" x2="1" y2="1">
          <stop offset="0" stop-color="var(--art-red)"/>
          <stop offset="1" stop-color="var(--art-red-deep)"/>
        </linearGradient>
      </defs>
      <path d="M0 0 C60 -4 150 20 210 90 C250 140 300 175 347 190 L347 206 L0 206 Z" fill="url(#front-art)"/>
    </svg>
  </section>

  <section class="card card--back" aria-label="Card back">
    <div class="wordmark">
      <span class="wordmark__name">VALCORNE</span>
      <span class="wordmark__line">HEALTH CARE MARKETING</span>
    </div>
    <svg class="flame-art" width="347" height="226" viewBox="0 0 347 226" role="img" aria-label="Red phoenix wing and flame illustration sweeping across the bottom of the card">
      <defs>
        <linearGradient id="back-art" x1="1" y1="0" x2="0" y2="1">
          <stop offset="0" stop-color="var(--art-red)"/>
          <stop offset="1" stop-color="var(--art-red-deep)"/>
        </linearGradient>
      </defs>
      <path d="M347 0 C280 -2 200 20 160 80 C120 140 50 180 0 200 L0 226 L347 226 Z" fill="url(#back-art)"/>
    </svg>
  </section>

</body>
</html>
```